http://www.brindlewares.com/ New Ecommerce Site

We are redesigning Brindlewares.com on shopvantly.com.

We need to get a design for the ecommerce site.

They have about 15-45 products and these are the menu items that they need on the pages.

Knives:
Kitchen Knives
Neck Knives
Outdoor Knives
Bluefinch Knives
Clearance Knives
Premium Knives
Misc. Product:
Waterstones
Books
DVDs
T-Shirts
Scissors
Bladesmithing School
Videos
Links
Testimonials/Feedback
Contact Dennis Form
Knife Care and Maintenance Tips
Knife Sharpening
Knife Archives
Kitchen Knife Archives

We need several pages designed.

- Category Page
- Single Item page
- Knive Archive Pages (This is where old knives are stored that are not being sold anymore)
- Featured Product pages.
- Information pages
- checkout

The design has to be VERY elagant, like vostel.com.
And it has to be very easy to navigate and buy items like http://bladesgoquick.com/

Thanks,
Peter Hollis

Requirements
Must have
• Must be very elegant, and have the menu items somewhere on the pages.

```html
<!DOCTYPE html>
<html lang="en">
<head>
<meta charset="utf-8">
<title>Brindle Wares – Knives</title>
<link href="https://fonts.googleapis.com/css2?family=Source+Sans+3:wght@400;600&family=Oswald:wght@500&display=swap" rel="stylesheet">
<style>
:root{
  --ink:#333;
  --muted:#555;
  --red:#a30f12;
  --red-dark:#8f0b0e;
  --topbar:#232323;
  --band:#eeeeee;
  --line:#dddddd;
  --card-line:#e6e6e6;
  --footer:#ececec;
  --footer-dark:#1d1d1d;
  --btn:#e9e9e9;
}
*{box-sizing:border-box;margin:0;padding:0}
html,body{width:860px;height:1200px;overflow:hidden}
body{font-family:"Source Sans 3",Arial,sans-serif;color:var(--ink);background:#fff;position:relative;font-size:12px}
a{color:inherit;text-decoration:none}
.wrap{position:absolute;left:62px;width:735px}

.topbar{position:absolute;top:0;left:0;width:860px;height:36px;background:var(--topbar);color:#fff}
.account-links{position:absolute;left:82px;top:11px;font-size:10.5px;font-weight:600;letter-spacing:.2px}
.account-links span{margin:0 8px;color:#ccc}
.cart{position:absolute;right:62px;top:11px;font-size:11.5px;display:flex;align-items:center;gap:6px}

.header{position:absolute;top:36px;left:0;width:860px;height:80px;border-bottom:1px solid var(--line)}
.brand{position:absolute;left:62px;top:8px;color:#8a8a8a;font-size:25px;line-height:23px;letter-spacing:1px;text-transform:uppercase}
.tagline{position:absolute;left:62px;top:61px;font-size:8.5px;color:#555}
.search{position:absolute;right:62px;top:27px;width:163px;height:25px;border:1px solid #ccc;border-radius:2px;font-size:9.5px;font-style:italic;color:#999;padding:5px 4px}
.search svg{position:absolute;right:7px;top:6px}

.mainnav{position:absolute;top:117px;left:0;width:860px;height:42px;background:var(--band);display:flex;align-items:center;padding-left:70px;font-size:11.5px;color:#333}
.mainnav a{padding:0 13px;border-right:1px dotted #c9c9c9;line-height:16px}
.mainnav a:first-child{padding-left:13px}
.mainnav a:last-child{border-right:0}

.hero{position:absolute;top:159px;left:0;width:860px;height:308px;background:linear-gradient(115deg,#7a4a1c 0%,#b77a2e 30%,#caa06a 50%,#9a5a22 75%,#5e3515 100%)}
.hero-caption{position:absolute;left:64px;top:163px;width:331px;height:124px;background:rgba(230,224,214,.72);padding:14px 14px}
.hero-caption h2{font-family:"Oswald",sans-serif;font-weight:500;font-size:22px;color:#333;letter-spacing:.3px;line-height:24px}
.hero-caption h3{font-weight:400;font-size:16px;color:#222;margin-top:6px}
.hero-caption p{font-size:11px;line-height:18px;color:#333;margin-top:6px}
.dots{position:absolute;right:72px;top:294px;display:flex;gap:4px}
.dots i{width:8px;height:8px;border-radius:50%;background:#fff}
.dots i:first-child{background:#888}

.section-title{position:absolute;top:492px;font-size:15px;font-weight:600;color:var(--red);letter-spacing:.3px}

.categories{position:absolute;left:62px;top:528px;width:198px;box-shadow:0 1px 4px rgba(0,0,0,.18)}
.categories li{list-style:none;height:34.4px;border-bottom:1px solid #eee;display:flex;align-items:center;justify-content:space-between;padding:0 12px;font-size:13px;color:#333;background:linear-gradient(#fff,#f7f9fa)}
.categories li.active{background:var(--red);color:#fff}
.arrow{width:17px;height:17px;border-radius:50%;border:1px solid #ddd;background:#fff;display:flex;align-items:center;justify-content:center}
.active .arrow{background:#333;border-color:#333}

.care{position:absolute;left:61px;top:807px;width:200px;height:159px;border:1px solid #ddd}
.care h4{height:33px;background:var(--red);color:#fff;font-weight:400;font-size:14.5px;padding:7px 13px}
.care p{font-size:9.5px;line-height:15.5px;color:#333;padding:10px 10px 0}
.care .email{margin:10px 10px 0;height:26px;border:1px solid #ccc;font-size:9.5px;color:#888;padding:6px 7px}
.care .subscribe{position:absolute;right:10px;bottom:14px;background:var(--red);color:#fff;font-size:10.5px;padding:4px 10px}

.card{position:absolute;width:159px;height:209px;border:1px solid var(--card-line);text-align:center}
.card .photo{width:120px;height:100px;margin:14px auto 0;border-radius:3px}
.card h5{font-weight:400;font-size:12.5px;color:var(--red-dark);margin-top:10px}
.card p{font-size:10.5px;line-height:18px;color:#444;text-align:left;padding:3px 11px 0}
.card .buy{display:flex;align-items:center;justify-content:space-between;padding:6px 11px 0}
.card .price{font-size:11.5px;color:#222}
.card .add{background:var(--btn);color:#555;font-size:9.5px;padding:3px 10px;margin-right:5px}
.steel{background:linear-gradient(135deg,#fff 10%,#d8d8d8 45%,#333 75%,#fff 90%)}
.blue{background:linear-gradient(160deg,#fff 15%,#dcdcdc 45%,#3c6fb0 70%,#fff 85%)}
.tiger{background:linear-gradient(135deg,#fff 5%,#c8701e 35%,#222 65%,#fff 90%)}
.dark{background:linear-gradient(160deg,#fff 10%,#333 40%,#111 65%,#fff 90%)}
.pink{background:linear-gradient(145deg,#fff 10%,#e8e8e8 45%,#e39acb 72%,#fff 90%)}

.footer{position:absolute;top:995px;left:0;width:860px;height:150px;background:var(--footer)}
.fcol{position:absolute;top:13px;font-size:9.5px;color:#333}
.fcol h6{font-size:11.5px;font-weight:400;margin-bottom:6px}
.fcol li{list-style:none;line-height:20.6px}
.newsletter-field{position:absolute;left:654px;top:49px;width:145px;height:25px;background:#c9c9c9;color:#888;font-size:15px;text-align:right;padding:1px 6px}
.social{position:absolute;left:654px;top:94px;display:flex;gap:2px}
.social i{width:20px;height:20px;border-radius:50%;background:#8d8d8d;border:1px solid #777}
.bottombar{position:absolute;top:1145px;left:0;width:860px;height:55px;background:var(--footer-dark);color:#ddd;font-size:9.5px;padding:26px 63px}
</style>
</head>
<body>

<div class="topbar">
  <nav class="account-links"><a>MY ACCOUNT</a><span>|</span><a>SIGN IN</a><span>|</span><a>CHECK OUT</a><span>|</span><a>CONTACT US</a></nav>
  <div class="cart">
    <svg width="14" height="12" viewBox="0 0 14 12"><path d="M0 1h2.5l2 7h7l1.5-5H4" fill="none" stroke="#ccc" stroke-width="1.2"/><circle cx="5.5" cy="10.5" r="1" fill="#ccc"/><circle cx="10.5" cy="10.5" r="1" fill="#ccc"/></svg>
    Cart (0) items
  </div>
</div>

<header class="header">
  <div class="brand">Brindle<br>Wares</div>
  <div class="tagline">17th Generation Tanekawa Bladesmith</div>
  <div class="search">Search..
    <svg width="11" height="11" viewBox="0 0 11 11"><circle cx="4.5" cy="4.5" r="3.5" fill="none" stroke="#888" stroke-width="1.4"/><path d="M7 7l3 3" stroke="#888" stroke-width="1.6"/></svg>
  </div>
</header>

<nav class="mainnav">
  <a>HOME</a><a>ABOUT US</a><a>SHARPENING VIDEOS</a><a>KNIVES</a><a>TOOLS</a><a>INSTRUCTION</a><a>FAQ</a><a>NEWS</a><a>CONTACT US</a>
</nav>

<section class="hero" role="img" aria-label="Close-up photo of two kitchen knives with wrapped handles on a wooden board">
  <div class="hero-caption">
    <h2>OUTDOOR KNIVES</h2>
    <h3>DIGNISSIM PHARETRA ERO</h3>
    <p>Jerta baditaut onsequser untur magni dolores eoquie volup tate msequi nesciunt. Voluptatem accusantium dolorem.</p>
  </div>
  <div class="dots"><i></i><i></i><i></i><i></i></div>
</section>

<h2 class="section-title" style="left:62px">CATEGORIES</h2>
<h2 class="section-title" style="left:305px">PRODUCTS</h2>

<ul class="categories">
  <li class="active">Kitchen Knives<span class="arrow"><svg width="6" height="5"><path d="M0 2.5h5M3 .5l2 2-2 2" stroke="#fff" fill="none"/></svg></span></li>
  <li>Neck Knives<span class="arrow"><svg width="6" height="5"><path d="M0 2.5h5M3 .5l2 2-2 2" stroke="#555" fill="none"/></svg></span></li>
  <li>Outdoor Knives<span class="arrow"><svg width="6" height="5"><path d="M0 2.5h5M3 .5l2 2-2 2" stroke="#555" fill="none"/></svg></span></li>
  <li>Bluefinch Knives<span class="arrow"><svg width="6" height="5"><path d="M0 2.5h5M3 .5l2 2-2 2" stroke="#555" fill="none"/></svg></span></li>
  <li>Clearance Knives<span class="arrow"><svg width="6" height="5"><path d="M0 2.5h5M3 .5l2 2-2 2" stroke="#555" fill="none"/></svg></span></li>
  <li>Premium Knives<span class="arrow"><svg width="6" height="5"><path d="M0 2.5h5M3 .5l2 2-2 2" stroke="#555" fill="none"/></svg></span></li>
  <li>Misc. Product<span class="arrow"><svg width="6" height="5"><path d="M0 2.5h5M3 .5l2 2-2 2" stroke="#555" fill="none"/></svg></span></li>
</ul>

<aside class="care">
  <h4>Knife Care Tips</h4>
  <p>Enter your email id to receive the knife care tips and subscriptions.</p>
  <div class="email">Enter your Email Id</div>
  <a class="subscribe">SUBSCRIBE</a>
</aside>

<article class="card" style="left:305px;top:529px">
  <div class="photo steel" role="img" aria-label="Chef knife with black handle"></div>
  <h5>Neck Knives</h5><p>NasaFlo Unbreiakable Quantu mireax PtBait</p>
  <div class="buy"><span class="price">$146.00</span><a class="add">ADD TO CART</a></div>
</article>
<article class="card" style="left:471px;top:529px">
  <div class="photo blue" role="img" aria-label="Wide knife with blue handle"></div>
  <h5>Outdoor Knives</h5><p>NasaFlo Unbreiakable Quantu mireax PtBait</p>
  <div class="buy"><span class="price">$146.00</span><a class="add">ADD TO CART</a></div>
</article>
<article class="card" style="left:637px;top:529px">
  <div class="photo tiger" role="img" aria-label="Set of three knives with striped blades"></div>
  <h5>Clearance Knives</h5><p>NasaFlo Unbreiakable Quantu mireax PtBait</p>
  <div class="buy"><span class="price">$146.00</span><a class="add">ADD TO CART</a></div>
</article>
<article class="card" style="left:305px;top:758px">
  <div class="photo dark" role="img" aria-label="Set of three black knives"></div>
  <h5>Neck Knives</h5><p>NasaFlo Unbreiakable Quantu mireax PtBait</p>
  <div class="buy"><span class="price">$146.00</span><a class="add">ADD TO CART</a></div>
</article>
<article class="card" style="left:471px;top:758px">
  <div class="photo steel" role="img" aria-label="Small paring knife with black handle"></div>
  <h5>Premium Knives</h5><p>NasaFlo Unbreiakable Quantu mireax PtBait</p>
  <div class="buy"><span class="price">$146.00</span><a class="add">ADD TO CART</a></div>
</article>
<article class="card" style="left:637px;top:758px">
  <div class="photo pink" role="img" aria-label="White ceramic knife with pink handle"></div>
  <h5>Bluefinch Knives</h5><p>NasaFlo Unbreiakable Quantu mireax PtBait</p>
  <div class="buy"><span class="price">$146.00</span><a class="add">ADD TO CART</a></div>
</article>

<footer class="footer">
  <div class="fcol" style="left:66px"><h6>Customer Services</h6><ul><li>Shopping Guide</li><li>Contact Us</li><li>FAQ</li><li>Track My Order</li><li>Return Policy</li></ul></div>
  <div class="fcol" style="left:223px"><h6>My Account</h6><ul><li>Sign in | Register</li><li>Order History</li><li>Messages</li><li>Points &amp; Coupons, Gifts</li><li>RMA Request</li></ul></div>
  <div class="fcol" style="left:377px"><h6>Company Info</h6><ul><li>Legal window</li><li>About Us</li><li>Why Buy From Us</li><li>Security &amp; Privacy</li><li>Terms of Use</li></ul></div>
  <div class="fcol" style="left:516px"><h6>Partner Program</h6><ul><li>Wholesale</li><li>Affiliate Program</li><li>Partner links</li><li>Drop-shipping</li></ul></div>
  <div class="fcol" style="left:654px"><h6>Newsletter</h6></div>
  <div class="newsletter-field">&#8250;&#8250;</div>
  <div class="social"><i></i><i></i><i></i><i></i></div>
</footer>

<div class="bottombar">© 2013 Copyrights Reserved. All rights reserved.</div>

</body>
</html>
```